Web Design Project

Brightfold Publishing owns and operates a large number of editorial websites. These websites provides mostly consumers in the financial services space with information and price comparisons for a particular service.

Brightfold Publishing, as the holding company for each of these sites, currently has no website. We need to build a website targeted towards potential partners for our websites. The idea being that when we start a conversation with a partner, they can view our site and obtain some basic information about who we are.

The structure of the site is to be very simple, containing only a brief description about who we are, our contact details and a list of some of our websites:
• CoverVault.net.au
• MotorPolicyCheck.com.au
• DwellingCoverCheck.com.au
• MedicalCoverCheck.com.au
• LegacyCoverCheck.com.au
• JourneyCoverCheck.com.au
• AnimalCoverCheck.com.au
• PrivateLendingCheck.com.au
• MobileCoolingUnit.com.au
• FixedSavingsYield.com.au
• ThriftyHousehold.com.au
• CoinNana.com.au
• TameYourPlastic.com.au
• PurseMinder.com.au
• ThirdPartyClaimsCoverNational.com.au
• Trade-Cover.com.au
• MotorPolicyProviders.com.au
• MedicalCoverProviders.com.au
• DwellingCoverHub.com
• LegacyCoverHub.com
• EarningsShieldCoverHub.com
• MedicalCoverHub.com
• AnimalCoverHub.com
• PrivateLendingHub.com
• ChargePlasticHub.com
• DwellingLendingHub.com
• RetireNestEgg.net.au

The design of the site should say 'Internet company', 'professional', 'fresh thinking'. The design should not look like a corporate site that you would see from any corporate services business with images of people in suits. We are ultimately an Internet business and there should be a unique feel to the site.

We are open to a suggestion of a colour pallet as the holding company does not have an established logo.

Some sites that we like are:

http://www.quillmarsh-studio.co.uk/#home
http://previewbox00.layoutdock.example/wt_52418/index.html
http://previewbox00.layoutdock.example/wordpress_61942/
http://ponderloop.example/
http://www.brindlux.example/
http://www.tobiasvrankel.example/
http://www.slickfrontdoors.example/Corporate/design-ideas-detail.html?id=4197
http://pairmint.example/
http://orvendal.example/

Reason: Hi all, Apologies, but I need to extend the timeline. One of our key stakeholders is away for the next week. There are a few good designs that we have received to date and there are some tweaks that we would like to see before making a final decision. Thank you to everyone that has submitted designs - Have a great new year. Derek

Reason: Sorry to have to delay the deadline on this, but we did not find anything in the designs really resonated with us. We will have a further think about the existing designs that have been submitted and how we can provide more specific feedback to the designers to make some modifications to the designs.

Target Market(s)

We are targeting insurance companies / brokers that we are talking to. The idea is that we show a professional face to them.

Industry/Entity Type

Financial

Requirements
Must have
• Home Page (possibly integrated with About us details)
Contact Us
Our Sites

```html
<!DOCTYPE html>
<html lang="en">
<head>
<meta charset="utf-8">
<title>Brightfold Publishing</title>
<link href="https://fonts.googleapis.com/css2?family=Cinzel:wght@400&family=Andada+Pro:wght@400&family=Arimo:wght@400&display=swap" rel="stylesheet">
<style>
  :root {
    --top-grey: #e3e3e3;
    --band-blue: #003a6e;
    --brand-slate: #4a6690;
    --nav-blue: #0a4f98;
    --text-dark: #333333;
    --footer-grey: #5a5a5a;
    --dot-grey: #a0a0a0;
    --dot-active: #3d5b88;
    --white: #ffffff;
    --link-blue: #7fb9ee;
    --sky-light: #eaf6ff;
    --sky-mid: #b4dcf7;
    --sky-deep: #7cc0ef;
  }
  * { margin: 0; padding: 0; box-sizing: border-box; }
  html, body { width: 1200px; height: 825px; overflow: hidden; }
  body { position: relative; background: var(--white); font-family: "Andada Pro", Georgia, serif; color: var(--text-dark); }

  .band-top { position: absolute; left: 0; top: 0; width: 1200px; height: 110px; background: var(--top-grey); }
  .band-blue { position: absolute; left: 0; top: 110px; width: 1200px; height: 358px; background: var(--band-blue); }
  .band-body { position: absolute; left: 0; top: 468px; width: 1200px; height: 274px; background: linear-gradient(#f4f5f6, #ffffff 75%); }

  .brand { position: absolute; left: 224px; top: 18px; font-family: "Cinzel", Georgia, serif; font-size: 33px; letter-spacing: 0.5px; color: var(--brand-slate); white-space: nowrap; }

  .main-nav { position: absolute; left: 680px; top: 20px; width: 294px; height: 35px; border: 1px solid #a9a9a9; border-radius: 4px; background: linear-gradient(#f3f3f3, #cfcfcf); display: flex; align-items: center; padding-left: 7px; gap: 3px; font-family: "Arimo", Arial, sans-serif; font-size: 15px; }
  .main-nav a { color: #1d1d1d; text-decoration: none; padding: 4px 7px; white-space: nowrap; }
  .main-nav a.is-current { background: linear-gradient(#2a6fc0, var(--nav-blue)); color: var(--white); border-radius: 3px; padding: 5px 8px; }

  .hero { position: absolute; left: 224px; top: 81px; width: 751px; height: 430px; border: 1px solid #c9d6e4;
    background:
      radial-gradient(ellipse 40% 30% at 30% 30%, rgba(255,255,255,0.85), rgba(255,255,255,0) 70%),
      radial-gradient(ellipse 60% 45% at 50% 85%, rgba(255,255,255,0.9), rgba(255,255,255,0) 75%),
      linear-gradient(160deg, var(--sky-mid) 0%, var(--sky-light) 45%, var(--sky-deep) 100%);
    box-shadow: 0 14px 18px -10px rgba(0,0,0,0.35); }

  .slider-dots { position: absolute; left: 550px; top: 517px; display: flex; gap: 3px; }
  .slider-dots span { width: 12px; height: 12px; border-radius: 50%; background: var(--dot-grey); }
  .slider-dots span.is-active { background: var(--dot-active); }

  .sites { position: absolute; left: 237px; top: 538px; width: 265px; }
  .sites h2, .about h2 { font-weight: 400; font-size: 21px; line-height: 26px; color: var(--brand-slate); }
  .site-list { list-style: none; margin-top: 6px; }
  .site-list li { position: relative; padding-left: 15px; font-size: 11.8px; line-height: 20.8px; color: #3a3a3a; white-space: nowrap; }
  .site-list li::before { content: ""; position: absolute; left: 1px; top: 7px; width: 5px; height: 5px; border-right: 1.6px solid #222; border-bottom: 1.6px solid #222; transform: rotate(-45deg); }
  .scroll-arrow { position: absolute; left: 485px; }

  .about { position: absolute; left: 519px; top: 539px; width: 453px; height: 162px; background: var(--white); padding: 0 0 0 28px; box-shadow: -8px 0 10px -8px rgba(0,0,0,0.2); }
  .about p { margin-top: 5px; font-size: 12.6px; line-height: 19.2px; color: #2f2f2f; white-space: nowrap; }

  .site-footer { position: absolute; left: 0; top: 742px; width: 1200px; height: 83px; background: var(--footer-grey); font-family: "Arimo", Arial, sans-serif; font-size: 10.5px; color: var(--white); }
  .copyright { position: absolute; left: 229px; top: 37px; white-space: nowrap; }
  .footer-nav { position: absolute; left: 726px; top: 36px; display: flex; gap: 12px; white-space: nowrap; }
  .footer-nav a { color: var(--white); text-decoration: none; }
  .footer-nav a.is-current { color: var(--link-blue); text-decoration: underline; }
</style>
</head>
<body>
  <div class="band-top"></div>
  <div class="band-blue"></div>
  <div class="band-body"></div>

  <div class="brand">Brightfold Publishing</div>

  <nav class="main-nav">
    <a href="#" class="is-current">Home</a>
    <a href="#">Our Sites</a>
    <a href="#">About</a>
    <a href="#">Contact Us</a>
  </nav>

  <div class="hero" role="img" aria-label="Illustration of groups of small figures standing in coloured rings around a glowing digital globe, on a light blue background"></div>

  <div class="slider-dots">
    <span class="is-active"></span><span></span><span></span><span></span><span></span><span></span><span></span><span></span>
  </div>

  <section class="sites">
    <h2>Our Sites</h2>
    <ul class="site-list">
      <li>CoverVault.net.au</li>
      <li>MotorPolicyCheck.com.au</li>
      <li>DwellingCoverCheck.com.au</li>
      <li>MedicalCoverCheck.com.au</li>
      <li>LegacyCoverCheck.com.au</li>
      <li>JourneyCoverCheck.com.au</li>
    </ul>
  </section>
  <svg class="scroll-arrow" style="top:569px" width="14" height="12" viewBox="0 0 14 12"><path d="M7 1 L13 11 L1 11 Z" fill="#c8c8c8" stroke="#8a8a8a"/></svg>
  <svg class="scroll-arrow" style="top:680px" width="14" height="12" viewBox="0 0 14 12"><path d="M1 1 L13 1 L7 11 Z" fill="#c8c8c8" stroke="#8a8a8a"/></svg>

  <section class="about">
    <h2>Brightfold Publishing</h2>
    <p>Brightfold Publishing is an Australian-based internet marketing<br>
    company. We specialise in attracting customers from our directory<br>
    of more than 100 sites to our network of trusted partners.&nbsp; Our skill<br>
    lies in generating targeted traffic to our range of websites and<br>
    identifying the right partners for each of the sites, ensuring that<br>
    the visitors to our sites get what they are looking for.</p>
  </section>

  <footer class="site-footer">
    <div class="copyright">Copyright @Brightfold Publishing2011.Com &nbsp;! All Rights Reserved.</div>
    <nav class="footer-nav">
      <a href="#" class="is-current">Home&nbsp;</a><span>|</span>
      <a href="#">Our Site</a><span>|</span>
      <a href="#">About Us</a><span>&nbsp;&nbsp;|</span>
      <a href="#">Contact us</a>
    </nav>
  </footer>
</body>
</html>
```